Using attached logo that has been created

Business card with logo that's attached. Maybe with water or the cartoon van in background. Looking for it to not be so plain and not too white.
Information to include;
Rodney Ashcombe
(555) 218-7730
Info@bramleypipeworks.example
www.bramleypipeworks.example
License # 4627195
Looking forward to the designs u come up with.
Thank you!
-Delphine
Target Market(s)
Plumbing
Industry/Entity Type
Plumbing
Contact Information for Business Card
Listed above

```html
<!DOCTYPE html>
<html lang="en">
<head>
<meta charset="utf-8">
<title>Bramley Pipeworks – Business Card</title>
<link rel="stylesheet" href="https://fonts.googleapis.com/css2?family=Oswald:wght@500;600&family=Noto+Serif:wght@400&display=swap">
<style>
  :root {
    --stage: #d9d9d9;
    --white: #ffffff;
    --blue: #0b5cb8;
    --blue-deep: #0a4ea3;
    --blue-light: #1a78cf;
    --yellow: #fdb913;
    --ink: #1a1a1a;
    --art-top: #e9eef5;
    --art-bottom: #c9a77a;
  }
  * { box-sizing: border-box; margin: 0; padding: 0; }
  html, body { width: 1200px; height: 800px; overflow: hidden; }
  body {
    background: var(--stage);
    position: relative;
    font-family: "Noto Serif", serif;
  }
  .card {
    position: absolute;
    border-radius: 18px;
    overflow: hidden;
    box-shadow: 0 10px 24px rgba(0,0,0,.18);
  }

  /* Front: portrait card */
  .card--front {
    left: 110px; top: 100px;
    width: 343px; height: 600px;
    background: var(--white);
  }
  .front__art {
    position: absolute; left: 40px; top: 30px;
    width: 263px; height: 310px;
    border-radius: 12px;
    background: linear-gradient(180deg, var(--art-top) 0%, #7fa6d9 45%, var(--art-bottom) 100%);
  }
  .front__stripe {
    position: absolute; left: 0; top: 350px;
    width: 100%; height: 10px;
    background: var(--yellow);
  }
  .front__panel {
    position: absolute; left: 0; top: 360px;
    width: 100%; height: 240px;
    background: radial-gradient(circle at 35% 55%, var(--blue-light) 0%, var(--blue) 55%, var(--blue-deep) 100%);
    color: var(--white);
    padding: 48px 36px 0;
  }
  .front__name {
    font-family: "Oswald", sans-serif;
    font-weight: 500;
    font-size: 30px;
    letter-spacing: .5px;
    text-transform: uppercase;
    margin-bottom: 14px;
  }
  .front__line {
    font-size: 14px;
    line-height: 1.55;
  }
  .front__license { margin-top: 10px; font-size: 14px; }

  /* Back: landscape card */
  .card--back {
    left: 510px; top: 228px;
    width: 600px; height: 343px;
    background: var(--yellow);
  }
  .back__art {
    position: absolute; left: 258px; top: 34px;
    width: 84px; height: 150px;
    border-radius: 10px;
    background: linear-gradient(180deg, #3b6fc4 0%, #2a5cb3 55%, #9c7b52 100%);
  }
  .back__name {
    position: absolute; left: 0; top: 196px; width: 100%;
    text-align: center;
    font-family: "Oswald", sans-serif;
    font-weight: 600;
    font-size: 34px;
    color: var(--blue-deep);
    text-transform: uppercase;
    letter-spacing: 1px;
  }
  .back__web {
    position: absolute; left: 0; bottom: 34px; width: 100%;
    text-align: center;
    font-size: 14px;
    letter-spacing: 7px;
    color: var(--ink);
    text-transform: uppercase;
  }
</style>
</head>
<body>
  <section class="card card--front">
    <div class="front__art" role="img" aria-label="Illustrated plumber holding a pipe wrench and a circular saw"></div>
    <div class="front__stripe"></div>
    <div class="front__panel">
      <h1 class="front__name">Rodney Ashcombe</h1>
      <p class="front__line">(555) 218-7730</p>
      <p class="front__line">Info@bramleypipeworks.example</p>
      <p class="front__line">bramleypipeworks.example</p>
      <p class="front__license">License # 4627195</p>
    </div>
  </section>

  <section class="card card--back">
    <div class="back__art" role="img" aria-label="Illustrated plumber mascot with wrench and saw"></div>
    <p class="back__name">Bramley Pipeworks &amp; More</p>
    <p class="back__web">www.bramleypipeworks.example</p>
  </section>
</body>
</html>
```